Business Card Design for a Personal Trainer

I need a business card design for my job as a personal trainer. It should have a unique, modern and exclusive design. On the front there should be only my logo with my name and my job. 0162/3819204 Tobias Lendhart Wiesengrundweg 14 80417 Munich Germany The most important contact information is the web adress. it can be bigger than the rest, but its not necessary. The card should be 8,5cmx5,5cm big. Font: Roboto. Colors: black, white, gray, 56c1ff.

```html
<!DOCTYPE html>
<html lang="de">
<head>
<meta charset="utf-8">
<title>Tobias Lendhart – Personal Trainer Visitenkarte</title>
<link href="https://fonts.googleapis.com/css2?family=Work+Sans:wght@400;500&display=swap" rel="stylesheet">
<style>
  :root{
    --backdrop:#3a332f;
    --card-black:#161616;
    --card-white:#ffffff;
    --ink:#111111;
    --foil:#8d8d8d;
    --photo-light:#d9d9d9;
    --photo-dark:#6e6e6e;
    --band:#2b2b2b;
  }
  html,body{margin:0;padding:0;overflow:hidden;}
  body{
    width:1200px;height:715px;background:var(--backdrop);
    font-family:"Work Sans",Roboto,Arial,sans-serif;position:relative;
  }
  .card{
    position:absolute;top:190px;width:520px;height:336px;
    box-shadow:0 10px 28px rgba(0,0,0,.45);overflow:hidden;
  }
  .lockup{display:inline-flex;flex-direction:column;align-items:stretch;white-space:nowrap;}
  .brand-name{
    display:flex;align-items:center;justify-content:center;
    font-weight:500;text-transform:uppercase;
  }
  .brand-mark{background:currentColor;display:inline-block;flex:none;}
  .brand-role{
    display:flex;align-items:center;gap:10px;
    text-transform:uppercase;white-space:nowrap;
  }
  .brand-role::before,.brand-role::after{content:"";flex:1 1 20px;height:1px;background:currentColor;}

  /* front */
  .card--front{left:50px;background:var(--card-black);}
  .front-wrap{position:absolute;left:0;right:0;top:122px;text-align:center;color:var(--foil);}
  .card--front .brand-name{gap:12px;font-size:30px;letter-spacing:1px;}
  .card--front .brand-mark{width:14px;height:14px;}
  .card--front .brand-role{margin-top:6px;font-size:13px;letter-spacing:5px;}

  /* back */
  .card--back{left:630px;background:var(--card-white);color:var(--ink);}
  .portrait{
    position:absolute;left:40px;top:40px;width:210px;height:296px;
    background:linear-gradient(180deg,var(--photo-light) 0%,var(--photo-dark) 70%,#4a4a4a 100%);
  }
  .name-band{
    position:absolute;left:0;top:240px;width:250px;height:52px;
    background:var(--band);color:#fff;padding:8px 0 0 56px;box-sizing:border-box;
  }
  .name-band .band-name{font-size:15px;font-weight:500;letter-spacing:1px;text-transform:uppercase;}
  .name-band .band-role{font-size:12px;margin-top:2px;}
  .back-wrap{position:absolute;left:270px;top:96px;width:240px;text-align:center;}
  .card--back .brand-name{gap:8px;font-size:19px;letter-spacing:.5px;}
  .card--back .brand-mark{width:10px;height:10px;}
  .card--back .brand-role{margin-top:5px;font-size:9px;letter-spacing:3px;gap:8px;}
  .contact{position:absolute;left:290px;top:170px;font-size:12.5px;line-height:19px;}
  .address{margin-bottom:10px;}
  .contact-row{display:grid;grid-template-columns:48px 12px auto;white-space:nowrap;}
</style>
</head>
<body>
  <section class="card card--front" aria-label="Vorderseite">
    <div class="front-wrap">
      <div class="lockup">
        <div class="brand-name"><span class="brand-mark"></span>Tobias Lendhart</div>
        <div class="brand-role">Personal Trainer</div>
      </div>
    </div>
  </section>

  <section class="card card--back" aria-label="Rückseite">
    <div class="portrait" role="img" aria-label="Schwarzweiß-Porträtfoto des Trainers mit verschränkten Armen"></div>
    <div class="name-band">
      <div class="band-name">Tobias Lendhart</div>
      <div class="band-role">Personal Trainer</div>
    </div>
    <div class="back-wrap">
      <div class="lockup">
        <div class="brand-name"><span class="brand-mark"></span>Tobias Lendhart</div>
        <div class="brand-role">Personal Trainer</div>
      </div>
    </div>
    <div class="contact">
      <div class="address">Wiesengrundweg 14<br>80417 München</div>
      <div class="contact-row"><span>Phone</span><span>:</span><span>0162/3819204</span></div>
      <div class="contact-row"><span>Email</span><span>:</span><span>info@tobiaslendhart.de</span></div>
      <div class="contact-row"><span>Web</span><span>:</span><span>www.tobiaslendhart.de</span></div>
    </div>
  </section>
</body>
</html>
```